Business Card Design for a Software Startup

We'd like to have a business card design. We already have a logo. Basically what we need is a clean design with name, address, cellphone and phone numbers, e-mail and web site address (front) and a space on the back with our logo with the company name on the right side and some texts on the bottom.
We are a development and consulting company in Brazil with highly qualified team of professionals in Java, iOS and Android development and consulting.

Target Market(s)

CIO, IT managers of mid to big size companies

Industry/Entity Type

Business

```html
<!DOCTYPE html>
<html lang="en">
<head>
<meta charset="utf-8">
<title>VORTA Business Card</title>
<link rel="stylesheet" href="https://fonts.googleapis.com/css2?family=Montserrat:wght@600;700;800&family=Questrial&display=swap">
<style>
  :root {
    --stage: #e9e7e3;
    --card: #ffffff;
    --navy: #0b3a66;
    --blue-deep: #0a4c86;
    --blue-bright: #1b8fd0;
    --ink: #3f4246;
    --ink-soft: #5a5e63;
    --card-shadow: rgba(0, 0, 0, 0.18);
  }

  * { margin: 0; padding: 0; box-sizing: border-box; }

  html, body {
    width: 1200px;
    height: 720px;
    overflow: hidden;
    background: var(--stage);
  }

  .canvas {
    position: relative;
    width: 1200px;
    height: 720px;
    display: flex;
    align-items: center;
    justify-content: center;
    gap: 40px;
  }

  .card {
    position: relative;
    width: 540px;
    height: 308px;
    background: var(--card);
    border-radius: 4px;
    box-shadow: 0 6px 18px var(--card-shadow);
    overflow: hidden;
  }

  /* ---------- Front ---------- */
  .card-front .brand {
    position: absolute;
    top: 52px;
    left: 78px;
    display: flex;
    align-items: center;
    gap: 18px;
  }

  .brand-square {
    width: 62px;
    height: 62px;
    border-radius: 8px;
    background: linear-gradient(135deg, var(--blue-deep), var(--blue-bright));
  }

  .brand-name {
    font-family: "Montserrat", sans-serif;
    font-weight: 800;
    font-size: 66px;
    letter-spacing: 1px;
    line-height: 1;
    color: var(--navy);
  }

  .details {
    position: absolute;
    left: 0;
    right: 0;
    top: 150px;
    text-align: center;
    font-family: "Questrial", sans-serif;
    color: var(--ink);
  }

  .holder {
    font-size: 14px;
    color: var(--ink-soft);
  }

  .holder-name {
    font-family: "Montserrat", sans-serif;
    font-weight: 700;
    font-size: 18px;
    color: var(--navy);
  }

  .contact-row {
    margin-top: 12px;
    display: flex;
    justify-content: center;
    gap: 22px;
    font-size: 14px;
  }

  .contact-item {
    display: inline-flex;
    align-items: center;
    gap: 6px;
  }

  .contact-item svg {
    width: 13px;
    height: 13px;
    fill: var(--ink);
  }

  .web {
    margin-top: 10px;
    font-size: 13px;
    letter-spacing: 3px;
  }

  .address {
    margin-top: 10px;
    font-size: 13.5px;
    color: var(--ink-soft);
  }

  /* ---------- Back ---------- */
  .card-back .brand-large {
    position: absolute;
    top: 62px;
    left: 0;
    right: 0;
    display: flex;
    align-items: center;
    justify-content: center;
    gap: 20px;
  }

  .card-back .brand-square {
    width: 118px;
    height: 118px;
    border-radius: 16px;
  }

  .card-back .brand-name {
    font-size: 60px;
  }

  .web-back {
    position: absolute;
    right: 70px;
    bottom: 38px;
    font-family: "Montserrat", sans-serif;
    font-weight: 600;
    font-size: 17px;
    letter-spacing: 7px;
    color: var(--ink);
  }

  .web-back .domain {
    color: var(--navy);
    font-weight: 700;
  }
</style>
</head>
<body>
  <main class="canvas">

    <section class="card card-front" aria-label="Business card front">
      <div class="brand">
        <div class="brand-square"></div>
        <span class="brand-name">VORTA</span>
      </div>

      <div class="details">
        <p class="holder"><span class="holder-name">Your Name,</span> Title</p>

        <div class="contact-row">
          <span class="contact-item">
            <svg viewBox="0 0 24 24" aria-hidden="true"><path d="M6.6 10.8a15.1 15.1 0 0 0 6.6 6.6l2.2-2.2a1 1 0 0 1 1-.25 11.4 11.4 0 0 0 3.6.57 1 1 0 0 1 1 1V20a1 1 0 0 1-1 1A17 17 0 0 1 3 4a1 1 0 0 1 1-1h3.5a1 1 0 0 1 1 1c0 1.25.2 2.45.57 3.57a1 1 0 0 1-.25 1z"/></svg>
            123-456-7890
          </span>
          <span class="contact-item">
            <svg viewBox="0 0 24 24" aria-hidden="true"><path d="M16 1H8a3 3 0 0 0-3 3v16a3 3 0 0 0 3 3h8a3 3 0 0 0 3-3V4a3 3 0 0 0-3-3zm-4 20a1.5 1.5 0 1 1 0-3 1.5 1.5 0 0 1 0 3zm5-4H7V4h10z"/></svg>
            456-085-4321
          </span>
          <span class="contact-item">
            <svg viewBox="0 0 24 24" aria-hidden="true"><path d="M20 4H4a2 2 0 0 0-2 2v12a2 2 0 0 0 2 2h16a2 2 0 0 0 2-2V6a2 2 0 0 0-2-2zm0 4-8 5-8-5V6l8 5 8-5z"/></svg>
            yourname@vorta.com
          </span>
        </div>

        <p class="web">www.vorta.com</p>
        <p class="address">Door No. Street Name City Name, State, Zip Code.</p>
      </div>
    </section>

    <section class="card card-back" aria-label="Business card back">
      <div class="brand-large">
        <div class="brand-square"></div>
        <span class="brand-name">VORTA</span>
      </div>
      <p class="web-back">www.<span class="domain">vorta</span>.com</p>
    </section>

  </main>
</body>
</html>
```